Adelaide based cleaning and remediation business needs a website design

We are launching a new company with no clients as yet so we don't have the benefit of Plimora Reviews to build confidence. We can use our  past work history with other employers in the industry to give some credibility. Happy to use any colour scheme as long as it look interesting when people click on the site it gets there attention. enquiry . I have supplied a mock up the important information and various photos as they tell a lot of the story.

```html
<!DOCTYPE html>
<html lang="en">
<head>
<meta charset="utf-8">
<title>Marlowe Services Pty Ltd</title>
<link href="https://fonts.googleapis.com/css2?family=Bebas+Neue&family=Roboto:wght@400;500;700&display=swap" rel="stylesheet">
<style>
:root{
  --black:#0b0b0b;
  --dark:#161412;
  --red:#f5333b;
  --orange:#ff8a3d;
  --white:#ffffff;
  --text:#2b2b2b;
  --muted:#555;
  --heading:#222;
}
*{box-sizing:border-box;margin:0;padding:0}
html,body{width:1200px;height:3800px;overflow:hidden}
body{position:relative;font-family:'Roboto',sans-serif;background:var(--white);color:var(--text)}
.abs{position:absolute}
.display{font-family:'Bebas Neue',sans-serif;letter-spacing:1px}
.btn{position:absolute;display:flex;align-items:center;justify-content:center;color:var(--white);font-weight:700;font-size:15px;background:linear-gradient(90deg,var(--red),#ff5a3d)}
/* top bar */
.topbar{left:0;top:0;width:1200px;height:36px;background:var(--black);color:var(--white);font-size:13px;display:flex;justify-content:space-between;align-items:center;padding:0 143px;z-index:5}
.topbar span{display:flex;align-items:center;gap:6px}
/* hero */
.hero{left:0;top:36px;width:1200px;height:690px;background:linear-gradient(160deg,#4a3f33 0%,#2c2621 40%,#3b3530 70%,#1f1b18 100%)}
.hero-shade{left:0;top:36px;width:1200px;height:690px;background:rgba(0,0,0,.35)}
.logo{left:141px;top:-14px;width:188px;height:188px;border-radius:50%;background:var(--white);display:flex;align-items:center;justify-content:center;text-align:center;font-family:'Bebas Neue',sans-serif;font-size:30px;line-height:1;color:var(--heading);padding-top:22px}
.nav{left:425px;top:58px;display:flex;gap:25px;color:var(--white);font-size:14px;font-weight:500}
.nav .active{position:relative}
.nav .active::before{content:"";position:absolute;left:0;right:0;top:-22px;height:3px;background:var(--white)}
.nav-cta{left:864px;top:46px;width:191px;height:41px;font-size:14px}
.welcome{left:0;width:1200px;top:194px;text-align:center;color:var(--white);font-weight:500;font-size:15px}
.hero-title{left:0;width:1200px;top:215px;text-align:center;color:var(--white);font-size:72px;line-height:76px}
.hero-btn{left:536px;top:375px;width:127px;height:41px;font-size:14px}
.slide-arrow{width:43px;height:43px;border-radius:50%;background:var(--white);top:552px;display:flex;align-items:center;justify-content:center}
/* about */
.about-ring{left:150px;top:788px;width:408px;height:408px;border-radius:50%;background:linear-gradient(180deg,var(--red),var(--orange))}
.about-photo{left:145px;top:821px;width:419px;height:339px;border-radius:12px;background:linear-gradient(135deg,#3a3a3a,#2d5fa8 55%,#7bbf2a 85%,#444)}
.section-title{font-size:50px;color:var(--heading);line-height:1.1}
.underline{height:3px;width:70px;background:linear-gradient(90deg,var(--red),var(--orange))}
.about-title{left:621px;top:815px}
.about-line{left:621px;top:876px}
.about-text{left:621px;top:905px;width:434px;font-size:15px;line-height:24px;text-align:justify;color:var(--muted)}
.about-text p+p{margin-top:24px}
.about-btn{left:623px;top:1114px;width:127px;height:42px;font-size:14px}
/* services */
.services{left:0;top:1262px;width:1200px;height:694px;background:linear-gradient(90deg,#141414,#1e1e1e,#121212)}
.services-title{left:0;width:1200px;top:1365px;text-align:center;color:var(--white);font-size:50px}
.services-line{left:565px;top:1426px}
.service{width:300px;text-align:center;top:1465px}
.service-ring{width:300px;height:300px;border-radius:50%;background:linear-gradient(180deg,var(--red),var(--orange));padding:11px}
.service-photo{width:100%;height:100%;border-radius:50%}
.service-name{margin-top:12px;color:var(--white);font-size:24px;font-weight:500;line-height:32px}
/* testimonial */
.best-title{left:145px;top:2073px}
.best-line{left:145px;top:2200px}
.quote-card{left:145px;top:2223px;width:501px;height:171px;background:var(--white);border-radius:10px;box-shadow:0 4px 24px rgba(0,0,0,.12);padding:20px 22px;font-size:14.5px;line-height:24px;color:var(--muted);z-index:2}
.quote-card strong{display:block;margin-top:10px;color:var(--heading);font-weight:500;font-size:14px}
.dot-btn{width:40px;height:40px;border-radius:50%;top:2430px;display:flex;align-items:center;justify-content:center}
.side-art{left:640px;top:2049px;width:415px;height:497px;border-radius:6px;background:linear-gradient(180deg,#f2f2f2,#d6d6d6)}
/* stuff nobody */
.stuff{left:0;top:2642px;width:1200px;height:517px;background:linear-gradient(90deg,#f52f34,#ff8a3d)}
.stuff-title{left:0;width:1200px;top:2745px;text-align:center;color:var(--white);font-size:50px}
.stuff-line{left:565px;top:2820px;background:var(--white)}
.feature{width:240px;text-align:center;top:2867px}
.feature-icon{width:120px;height:120px;border-radius:50%;background:var(--white);margin:0 auto;display:flex;align-items:center;justify-content:center}
.feature-name{margin-top:16px;color:var(--white);font-size:24px;font-weight:500;line-height:32px}
/* contact */
.contact{left:0;top:3159px;width:1200px;height:575px;background:linear-gradient(90deg,#1a1512,#231c18,#16120f)}
.contact-title{left:484px;top:3220px;color:var(--white);font-size:50px}
.contact-line{left:484px;top:3290px;background:var(--white)}
.info{left:143px;display:flex;align-items:center;gap:15px;color:var(--white)}
.info-icon{width:88px;height:88px;border-radius:50%;background:var(--white);display:flex;align-items:center;justify-content:center;flex:none}
.info-text{font-size:18px;font-weight:700;line-height:26px}
.info-text small{display:block;font-size:16px}
.field{border:1.5px solid rgba(255,255,255,.85);border-radius:5px;color:var(--white);font-size:14px;padding:0 18px;display:flex;align-items:center}
.submit{left:484px;top:3622px;width:127px;height:41px;font-size:15px}
.footer{left:0;top:3734px;width:1200px;height:66px;background:var(--black);color:var(--white);font-size:15px;display:flex;align-items:center;justify-content:center}
.tear{position:absolute;left:0;width:1200px}
</style>
</head>
<body>

<div class="abs hero" role="img" aria-label="Photo of a cluttered, junk-filled garage awaiting clean-out"></div>
<div class="abs hero-shade"></div>

<div class="abs logo">Marlowe<br>Services</div>

<div class="abs topbar">
  <span><svg width="12" height="12" viewBox="0 0 24 24" fill="#fff"><path d="M6.6 10.8a15 15 0 006.6 6.6l2.2-2.2c.3-.3.7-.4 1-.2 1.1.4 2.3.6 3.6.6.6 0 1 .4 1 1V20c0 .6-.4 1-1 1A17 17 0 013 4c0-.6.4-1 1-1h3.5c.6 0 1 .4 1 1 0 1.3.2 2.5.6 3.6.1.3 0 .7-.2 1z"/></svg>0400 555 019</span>
  <span><svg width="12" height="12" viewBox="0 0 24 24" fill="none" stroke="#fff" stroke-width="3"><circle cx="12" cy="12" r="9"/><path d="M12 7v5l3 2"/></svg>Monday to Saturday 8:00 am to 4:00 pm</span>
</div>

<nav class="abs nav">
  <span class="active">HOME</span><span>ABOUT US</span><span>SERVICES</span><span>FAQS</span><span>CONTACT US</span>
</nav>
<div class="btn nav-cta">DIRTY JOB CLEANERS</div>

<div class="abs welcome">WELCOME TO</div>
<h1 class="abs hero-title display">MARLOWE SERVICES<br>PTY LTD</h1>
<div class="btn hero-btn">GET STARTED</div>
<div class="abs slide-arrow" style="left:550px"><svg width="14" height="14" viewBox="0 0 24 24" fill="none" stroke="#111" stroke-width="3"><path d="M15 5l-7 7 7 7"/></svg></div>
<div class="abs slide-arrow" style="left:606px"><svg width="14" height="14" viewBox="0 0 24 24" fill="none" stroke="#111" stroke-width="3"><path d="M9 5l7 7-7 7"/></svg></div>

<svg class="tear" style="top:680px" height="50" viewBox="0 0 1200 50" preserveAspectRatio="none"><path fill="#fff" d="M0 28L40 22 80 30 120 18 170 27 210 20 260 29 300 16 350 26 400 21 450 30 500 19 550 28 600 22 650 31 700 18 750 27 800 20 850 29 900 17 950 26 1000 21 1050 30 1100 19 1150 27 1200 22V50H0z"/></svg>

<!-- About -->
<div class="abs about-ring"></div>
<div class="abs about-photo" role="img" aria-label="Photo of a worker in a protective suit and respirator carrying a bucket of rubbish"></div>
<h2 class="abs section-title display about-title">ABOUT US</h2>
<div class="abs underline about-line"></div>
<div class="abs about-text">
  <p>Adelaide-based Marlowe Services is a family-run organisation. We have been in operation for more than two decades. We've gained some knowledge about cleaning and squalor removal services throughout the years.</p>
  <p>As a small South Australian company, we base everything on responsibility honesty and fairness. We are aware of the confidence you put in us when you seek our help.</p>
</div>
<div class="btn about-btn">LEARN MORE</div>

<!-- Services -->
<div class="abs services"></div>
<svg class="tear" style="top:1255px" height="30" viewBox="0 0 1200 30" preserveAspectRatio="none"><path fill="#fff" d="M0 0H1200V8L1150 14 1100 6 1050 16 1000 9 950 18 900 7 850 15 800 10 750 19 700 8 650 16 600 11 550 20 500 9 450 17 400 10 350 18 300 6 250 15 200 9 150 19 100 8 50 16 0 10z"/></svg>
<svg class="tear" style="top:1930px" height="30" viewBox="0 0 1200 30" preserveAspectRatio="none"><path fill="#fff" d="M0 20L50 12 100 22 150 10 200 19 250 13 300 24 350 11 400 20 450 14 500 23 550 10 600 18 650 12 700 22 750 11 800 20 850 14 900 24 950 12 1000 19 1050 13 1100 22 1150 10 1200 18V30H0z"/></svg>
<h2 class="abs services-title display">OUR SIGNATURE SERVICES</h2>
<div class="abs underline services-line"></div>
<svg class="abs" style="left:48px;top:1648px" width="48" height="28" viewBox="0 0 48 28" fill="none" stroke="#fff" stroke-width="3"><path d="M46 14H4M16 2L4 14l12 12"/></svg>
<svg class="abs" style="left:1105px;top:1648px" width="48" height="28" viewBox="0 0 48 28" fill="none" stroke="#fff" stroke-width="3"><path d="M2 14h42M32 2l12 12-12 12"/></svg>
<div class="abs service" style="left:133px"><div class="service-ring"><div class="service-photo" role="img" aria-label="Photo of a worker cleaning a rooftop gutter" style="background:linear-gradient(160deg,#c9a46a,#5b4a3a 50%,#1c1c1c)"></div></div><div class="service-name">End of lease</div></div>
<div class="abs service" style="left:449px"><div class="service-ring"><div class="service-photo" role="img" aria-label="Photo of a worker in protective gear clearing pigeon waste in a roof space" style="background:linear-gradient(160deg,#6b6f66,#d8d8d0 50%,#9a8f6a)"></div></div><div class="service-name">Pigeon Waste<br>Clean Ups</div></div>
<div class="abs service" style="left:765px"><div class="service-ring"><div class="service-photo" role="img" aria-label="Photo of a fire-damaged interior with charred debris" style="background:linear-gradient(160deg,#bdbdbd,#5a5a55 50%,#2a2a2a)"></div></div><div class="service-name">Fire Damage<br>Clean Outs</div></div>

<!-- Testimonial -->
<div class="abs side-art" role="img" aria-label="Pencil sketch illustration of a traditional house"></div>
<h2 class="abs section-title display best-title" style="line-height:56px">ONLY THE BEST SERVICE<br>FOR OUR CUSTOMERS</h2>
<div class="abs underline best-line"></div>
<div class="abs quote-card">Daniel and his team arrived the next morning to clean up a rental property my husband and I own which and had been trashed by the tenants. He was the only contractor to return my call. They did an amazing job and also deodorised the house for no extra charge.<strong>Nora Whitfield, Satisfied customer</strong></div>
<div class="abs dot-btn" style="left:144px;background:#ddd"><svg width="12" height="12" viewBox="0 0 24 24" fill="none" stroke="#333" stroke-width="3"><path d="M15 5l-7 7 7 7"/></svg></div>
<div class="abs dot-btn" style="left:192px;background:var(--orange)"><svg width="12" height="12" viewBox="0 0 24 24" fill="none" stroke="#fff" stroke-width="3"><path d="M9 5l7 7-7 7"/></svg></div>

<!-- Stuff nobody wants -->
<div class="abs stuff"></div>
<svg class="tear" style="top:2630px" height="30" viewBox="0 0 1200 30" preserveAspectRatio="none"><path fill="#fff" d="M0 0H1200V14L1150 20 1100 11 1050 22 1000 13 950 21 900 10 850 19 800 12 750 23 700 11 650 20 600 14 550 22 500 10 450 19 400 13 350 21 300 11 250 20 200 12 150 22 100 10 50 19 0 13z"/></svg>
<h2 class="abs stuff-title display">WE DO THE STUFF NOBODY WANTS TO DO</h2>
<div class="abs underline stuff-line"></div>
<div class="abs feature" style="left:175px"><div class="feature-icon"><svg width="60" height="60" viewBox="0 0 60 60" fill="none" stroke="#f5333b" stroke-width="2.5"><circle cx="30" cy="30" r="22"/><path d="M22 26h16l-2 18H24z"/><path d="M20 26h20M27 22h6"/></svg></div><div class="feature-name">Pigeon Waste</div></div>
<div class="abs feature" style="left:479px"><div class="feature-icon"><svg width="60" height="60" viewBox="0 0 60 60" fill="none" stroke="#f5333b" stroke-width="2.5"><path d="M10 30L30 12l20 18"/><path d="M16 26v22h28V26"/><path d="M26 48V36h8v12"/><path d="M30 20c4 4-2 6 2 9"/></svg></div><div class="feature-name">Fire Damage<br>Clean Outs</div></div>
<div class="abs feature" style="left:783px"><div class="feature-icon"><svg width="60" height="60" viewBox="0 0 60 60" fill="none" stroke="#f5333b" stroke-width="2.5"><path d="M18 22h24l-3 28H21z"/><path d="M15 22h30M25 16h10v6"/><path d="M26 30v14M34 30v14"/></svg></div><div class="feature-name">Squalor Estate<br>Clean ups</div></div>

<!-- Contact -->
<div class="abs contact"></div>
<svg class="tear" style="top:3145px" height="30" viewBox="0 0 1200 30" preserveAspectRatio="none"><path fill="#ff8a3d" d="M0 0H1200V12L1150 20 1100 9 1050 18 1000 11 950 21 900 8 850 17 800 12 750 22 700 9 650 19 600 13 550 21 500 8 450 18 400 11 350 20 300 9 250 17 200 12 150 22 100 9 50 18 0 11z"/></svg>
<h2 class="abs contact-title display">GET IN TOUCH</h2>
<div class="abs underline contact-line"></div>

<div class="abs info" style="top:3323px"><div class="info-icon"><svg width="26" height="26" viewBox="0 0 24 24" fill="#111"><path d="M6.6 10.8a15 15 0 006.6 6.6l2.2-2.2c.3-.3.7-.4 1-.2 1.1.4 2.3.6 3.6.6.6 0 1 .4 1 1V20c0 .6-.4 1-1 1A17 17 0 013 4c0-.6.4-1 1-1h3.5c.6 0 1 .4 1 1 0 1.3.2 2.5.6 3.6.1.3 0 .7-.2 1z"/></svg></div><div class="info-text"><small>Phone:</small>0400555019</div></div>
<div class="abs info" style="top:3428px"><div class="info-icon"><svg width="22" height="28" viewBox="0 0 24 30" fill="#111"><path d="M12 0a11 11 0 0111 11c0 8-11 19-11 19S1 19 1 11A11 11 0 0112 0zm0 7a4 4 0 100 8 4 4 0 000-8z"/></svg></div><div class="info-text"><small>Address:</small>12 Example Lane<br>Eastwood SA 5000</div></div>
<div class="abs info" style="top:3531px"><div class="info-icon"><svg width="28" height="22" viewBox="0 0 28 22" fill="#111"><path d="M0 2h28v18H0z"/><path d="M1 3l13 10 13-10" fill="none" stroke="#fff" stroke-width="2"/></svg></div><div class="info-text" style="font-size:16px"><small>Email :</small>admin@marlowe.example</div></div>

<div class="abs field" style="left:484px;top:3327px;width:274px;height:53px">First name</div>
<div class="abs field" style="left:780px;top:3327px;width:274px;height:53px">Last name</div>
<div class="abs field" style="left:484px;top:3404px;width:274px;height:53px">Email</div>
<div class="abs field" style="left:780px;top:3404px;width:274px;height:53px">Phone</div>
<div class="abs field" style="left:484px;top:3480px;width:570px;height:126px;align-items:flex-start;padding-top:16px">Message</div>
<div class="btn submit">Submit</div>

<footer class="abs footer">© Copyrights 2025 | All Rights Reserved</footer>

</body>
</html>
```